New B2C website design to help dads be better dads

DadHarbor is a website to help dads be the “best dad you can be.”

We require our website to be designed into a PSD format, no coding necessary.

The general concept is a two-page design. The first page is the login page, the second page is the home page. Once at the home page, rather than navigating to and from different pages, the user will push and pull through different visual and functional layers of the hierarchy. In theory, this should add to the user experience by having a visual anchor of where they are (through layered pagination) as well as improving loading times since the new information should only be a delta in data load versus a brand new page load.

The general look-and-feel we are going for is clean, simple, minimal. This means that the winning design will show us a good eye for web-optimized typography, good use of white (negative) space, and good use of a visually pleasing grid.

We require a total of 6 page "views" plus the landing page. We note that many of the views are similar to one another.
Landing page
Milestone view
Task view
Content view, articles
Content view, products
Search view
What's new view

Please review all of the additional information provided as well as the attachments for examples.

We provide the following websites as good references for:

Typography:
http://example-kelvorn.com/journal/

Use of white space:
http://www.trenvaskit.com/
http://moldrefin.com/

Example for “scrolling” page concept as well as good balance of color, typography, and white space:
http://www.qorbitalmeet.eu/

Please contact us with questions so that we can guide your design effort.
Updates

Hello designers,

The following information is added to help guide the design process:

1.  For the text dialogue below the landing page, please assume the following word count:
"why are we making dad harbor?": 250 words
"who are we?" 200 words
"what's the deal with the penguin logo?" 300 words

For the social media links, please see http://www.gravelplumbs.com/
Notice the floating "social" bar that is always to the right.  This is the concept we are going for, please try to implement this as you see fit. 

Target Market(s)

Fathers of young children ages 0-6 years old.

Industry/Entity Type

Product

Font styles to use
Sans Serif

Requirements
Must have
• Clean lines, minimal design concept

Incorporation of our logo (see attached document)

Header content is static for all views after landing page, see example

This page WILL be responsive, please keep that in mind when designing
The timeline bar should be to the left, with the timeline bar’s “milestones” also being responsive.

Designer is free to suggest font types, but any fonts used must be royalty-free and web-optimized. We request a minimum number of font types as well as fonts that load relatively fast. We reinforce that visually appealing typography is a significant factor in the winning design choice.

While we are not expecting the winning design to include code, please keep in mind that the final implementation needs to be optimized for desktop, tablet, and mobile platforms.

If you are using stock photography that is not generated by you, please provide where/how we can obtain imagery, as well as price.

All custom graphics must be available in original formats; Photoshop/GIMP layered files for layout design, and vector formats for logos, icons and other graphical elements.

Please incorporate “Blue” into design elements as you see fit, as the RGB 67 74 169 Blue is the primary color used in our brand. The complement to this blue is 255 202 0, a brownish orange. Feel free to use this color as well, although please keep it to a lesser amount.

Background color is your choice, do not feel the need to use the grey.
Should not have
• Excessive graphical content such that it affects loading times

Excessive use of too many font types such that it affects loading times

```html
<!DOCTYPE html>
<html lang="en">
<head>
<meta charset="utf-8">
<title>DadHarbor</title>
<link rel="stylesheet" href="https://fonts.googleapis.com/css2?family=Open+Sans:wght@300;400;600;700;800&family=Oswald:wght@500;600&display=swap">
<style>
:root{
  --brand-blue:#434aa9;
  --deep-navy:#1f2a6b;
  --accent-yellow:#ffca00;
  --ink:#1b1b1b;
  --body-ink:#2a2a2a;
  --white:#ffffff;
  --ring-blue:#6b7fd6;
  --ring-sky:#9fd3ef;
  --muted:#555b66;
}
*{box-sizing:border-box;margin:0;padding:0}
html,body{width:1200px;height:3151px;overflow:hidden;background:var(--white)}
body{font-family:"Open Sans",Arial,sans-serif;color:var(--body-ink);position:relative}

/* Hero */
.hero{position:absolute;left:0;top:0;width:1200px;height:704px;overflow:hidden}
.hero-photo{position:absolute;inset:0;background:
  radial-gradient(ellipse at 30% 20%,#a7c46a 0%,rgba(126,162,74,0) 55%),
  radial-gradient(ellipse at 45% 70%,#c49a78 0%,rgba(185,138,102,0) 55%),
  radial-gradient(ellipse at 85% 60%,#6b4a3a 0%,rgba(107,74,58,0) 50%),
  linear-gradient(160deg,#8fb05a 0%,#7a8f4a 40%,#9a7258 70%,#5a3e30 100%)}
.brand{position:absolute;left:30px;top:36px;display:flex;align-items:center;gap:10px}
.brand-dot{width:34px;height:34px;border-radius:50%;background:var(--brand-blue)}
.brand-name{font-weight:700;font-size:20px;color:var(--brand-blue)}
.tagline{position:absolute;left:32px;top:179px;width:698px;height:110px;background:rgba(20,20,20,.78);padding:6px 14px}
.tagline-title{font-family:"Oswald",Arial,sans-serif;font-weight:600;font-size:50px;line-height:58px;color:var(--accent-yellow);letter-spacing:.5px;white-space:nowrap}
.tagline-sub{font-size:25px;line-height:36px;color:var(--white);white-space:nowrap}
.login{position:absolute;left:32px;top:310px;width:304px;height:247px;background:rgba(255,255,255,.82);border-radius:6px;padding:16px 18px}
.login-field{display:flex;align-items:center;gap:8px;height:46px;background:var(--white);border:1px solid #c9ccd3;border-radius:3px;padding:0 12px;font-size:15px;color:#333;margin-bottom:22px}
.login-field svg{flex:none}
.login-forgot{font-size:12px;color:#222;margin:-8px 0 18px;display:flex;align-items:center;gap:4px}
.login-button{display:block;width:100%;height:48px;background:var(--deep-navy);color:var(--white);border:0;border-radius:3px;font-family:"Open Sans",Arial,sans-serif;font-weight:700;font-size:14px;letter-spacing:.3px}
.share-bar{position:absolute;right:0;top:179px;width:55px;height:254px;background:rgba(255,255,255,.88);border-radius:6px 0 0 6px;display:flex;flex-direction:column;align-items:center;padding-top:8px;gap:10px}
.share-label{font-size:12px;color:#333}
.share-dot{width:40px;height:40px;border-radius:50%;background:var(--brand-blue)}
.scroll-cue{position:absolute;left:564px;top:636px}

/* About */
.about-title{position:absolute;top:744px;left:0;width:1200px;text-align:center;font-weight:800;font-size:44px;color:var(--brand-blue);letter-spacing:.5px}

.story{position:absolute;left:0;width:1200px;overflow:hidden}
.story-heading{position:absolute;left:30px;font-weight:300;font-size:46px;line-height:56px;color:var(--ink)}
.story-text{position:absolute;left:32px;width:610px;font-size:14px;line-height:24.5px;color:var(--body-ink)}
.story-photo{position:absolute;border-radius:50%}
.story--why{top:861px;height:641px;background:linear-gradient(180deg,#d9dcdf 0%,#f4f5f6 35%,#ffffff 60%,#eceef0 100%)}
.story--who{top:1502px;height:651px;background:linear-gradient(180deg,#f7f8f9 0%,#ffffff 45%,#e6e9ec 100%)}
.story--logo{top:2153px;height:652px;background:var(--brand-blue)}
.story--logo .story-heading,.story--logo .story-text{color:var(--white)}
.why-photo{left:636px;top:50px;width:542px;height:542px;border:7px solid var(--ring-blue);background:radial-gradient(circle at 45% 45%,#c9a184 0%,#a98a78 40%,#8fa0c4 75%,#e8e9ec 100%)}
.who-photo{left:638px;top:54px;width:538px;height:538px;border:7px solid var(--ring-sky);background:linear-gradient(180deg,#bfe0ee 0%,#5aa9cf 45%,#3b88b8 70%,#86b8d0 100%)}
.logo-mark{position:absolute;left:680px;top:300px;width:440px;text-align:center;font-weight:700;font-size:76px;color:rgba(255,255,255,.9)}

/* Footer */
.footer{position:absolute;top:2805px;left:0;width:1200px;height:346px;background:var(--white);text-align:center}
.footer-kicker{position:absolute;top:44px;width:100%;font-size:14px;letter-spacing:3px;font-weight:600;color:#333}
.footer-title{position:absolute;top:82px;width:100%;font-weight:300;font-size:38px;letter-spacing:1px;color:var(--ink)}
.footer-email{position:absolute;top:150px;width:100%;font-weight:700;font-size:21px;color:var(--brand-blue)}
.footer-social{position:absolute;top:212px;left:0;width:100%;display:flex;justify-content:center;gap:36px}
.footer-social span{width:54px;height:54px;border-radius:50%;border:2px solid #d8dbe4;background:var(--white);position:relative}
.footer-social span::after{content:"";position:absolute;inset:14px;border-radius:50%;background:var(--brand-blue)}
.footer-legal{position:absolute;top:284px;width:100%;font-size:13px;color:var(--muted)}
</style>
</head>
<body>

<header class="hero">
  <div class="hero-photo" role="img" aria-label="Photo of a father lying on the grass lifting his smiling young son above him"></div>
  <div class="brand"><span class="brand-dot"></span><span class="brand-name">DadHarbor</span></div>
  <div class="tagline">
    <div class="tagline-title">BE THE BEST DAD YOU CAN BE</div>
    <div class="tagline-sub">The portal created exclusively for dads, by dads</div>
  </div>
  <form class="login">
    <div class="login-field">
      <svg width="18" height="18" viewBox="0 0 18 18"><circle cx="9" cy="5.5" r="4" fill="#434aa9"/><path d="M1.5 17c0-4.2 3.3-7 7.5-7s7.5 2.8 7.5 7z" fill="#434aa9"/></svg>
      Username
    </div>
    <div class="login-field">
      <svg width="18" height="18" viewBox="0 0 18 18"><rect x="3" y="8" width="12" height="9" rx="1.5" fill="#434aa9"/><path d="M5.5 8V5.5a3.5 3.5 0 0 1 7 0V8" fill="none" stroke="#434aa9" stroke-width="2"/></svg>
      Password
    </div>
    <div class="login-forgot"><svg width="8" height="8" viewBox="0 0 8 8"><path d="M2 1l4 3-4 3z" fill="#222"/></svg>Forgot login?</div>
    <button class="login-button" type="button">SIGN IN / REQUEST ACCESS</button>
  </form>
  <aside class="share-bar">
    <span class="share-label">Share</span>
    <span class="share-dot" aria-label="Share link one"></span>
    <span class="share-dot" aria-label="Share link two"></span>
    <span class="share-dot" aria-label="Share link three"></span>
    <span class="share-dot" aria-label="Share link four"></span>
  </aside>
  <svg class="scroll-cue" width="72" height="40" viewBox="0 0 72 40"><path d="M4 6l32 26L68 6" fill="none" stroke="#2b2f6e" stroke-width="5"/><path d="M14 6l22 18L58 6" fill="none" stroke="#2b2f6e" stroke-width="3" opacity=".6"/></svg>
</header>

<h1 class="about-title">ABOUT DAD HARBOR</h1>

<section class="story story--why">
  <h2 class="story-heading" style="top:52px">Why are we making dad harbor?</h2>
  <p class="story-text" style="top:124px">Lorem ipsum dolor sit amet, consectetur adipiscing elit, sed do eiusmod tempor incididunt ut labore et dolore magna aliqua. Ut enim ad minim veniam, quis nostrud exercitation ullamco laboris nisi ut aliqip ex ea comodo consquat. Duis aute irure dolor in reprehenderit in voptate velit esse cillum dolore eu fugiat nulla paritur. Excepteur sint occaecat cupidatat non proident, sunt in culpa qui officia deserunt mollit anim id est laborum. Lorem ipsum dolor sit amet, consectetur adipisicing elit, sed do eiusd tmor incididunt ut labore et doore magna aliqua. Ut enim ad minim veniam, quis nostrud exercitation ullamco laboris nisi ut aliquip ex ea commodo consequat. Duis aute irure dolor in reheerit in volute velit esse cillum dolore eu fugiat nulla paiatur. Exceptur sint occaecat cidatat non proident, sunt in culpa qui officia deerunt mollit anim id est laborum. Lorem ipsum door sit met, conttur adiscing elit, sed do eiumod tempor incidunt ut labore et dolore magna aliqua. Ut enim ad mnim veniam, quis nostud exercitation ullamco laboris nisi ut aliquip ex ea commodo consequat. Duis aute irure door in reprehenderit in voluptate velit esse cillum doore eu fugiat nulla pariatur. Excepteur sint occecat cupiatat non proident, sunt in culpa. ex ea commodo conequat. Duis aute irure door in reprehenderit in voluptate velit esse cillum doore eu fugiat nulla pariatur. Excepteur sint occecat cupiatat non proident, sunt in culpa.</p>
  <div class="story-photo why-photo" role="img" aria-label="Photo of a smiling father hugging his young son"></div>
</section>

<section class="story story--who">
  <h2 class="story-heading" style="top:54px">Who are we?</h2>
  <p class="story-text" style="top:124px">Lorem ipsum dolor sit amet, consectetur adipiscing elit, sed do eiusmod tempor incididunt ut labore et dolore magna aliqua. Ut enim ad minim veniam, quis nostrud exercitation ullamco laboris nisi ut aliqip ex ea comodo consquat. Duis aute irure dolor in reprehenderit in voptate velit esse cillum dolore eu fugiat nulla paritur. Excepteur sint occaecat cupidatat non proident, sunt in culpa qui officia deserunt mollit anim id est laborum. Lorem ipsum dolor sit amet, consectetur adipisicing elit, sed do eiusd tmor incididunt ut labore et doore magna aliqua. Ut enim ad minim veniam, quis nostrud exercitation ullamco laboris nisi ut aliquip ex ea commodo consequat. Duis aute irure dolor in reheerit in volute velit esse cillum dolore eu fugiat nulla paiatur. Exceptur sint occaecat cidatat non proident, sunt in culpa qui officia deerunt mollit anim id est laborum. Lorem ipsum door sit met, conttur adiscing elit, sed do eiumod tempor incidunt ut labore et dolore magna aliqua. Ut enim ad mnim veniam, quis nostud exercitation ullamco laboris nisi ut aliquip ex ea commodo consequat. Duis aute irure door in reprehenderit in voluptate velit esse cillum doore eu fugiat nulla pariatur. Excepteur sint occecat cupiatat non proident, sunt in culpa.</p>
  <div class="story-photo who-photo" role="img" aria-label="Photo of a father and two small children in sun hats sitting by the sea"></div>
</section>

<section class="story story--logo">
  <h2 class="story-heading" style="top:52px;width:640px">What's the deal with the penguin logo?</h2>
  <p class="story-text" style="top:172px">Lorem ipsum dolor sit amet, consectetur adipiscing elit, sed do eiusmod tempor incididunt ut labore et dolore magna aliqua. Ut enim ad minim veniam, quis nostrud exercitation ullamco laboris nisi ut aliqip ex ea comodo consquat. Duis aute irure dolor in reprehenderit in voptate velit esse cillum dolore eu fugiat nulla paritur. Excepteur sint occaecat cupidatat non proident, sunt in culpa qui officia deserunt mollit anim id est laborum. Lorem ipsum dolor sit amet, consectetur adipisicing elit, sed do eiusd tmor incididunt ut labore et doore magna aliqua. Ut enim ad minim veniam, quis nostrud exercitation ullamco laboris nisi ut aliquip ex ea commodo consequat. Duis aute irure dolor in reheerit in volute velit esse cillum dolore eu fugiat nulla paiatur. Exceptur sint occaecat cidatat non proident, sunt in culpa qui officia deerunt mollit anim id est laborum. Lorem ipsum door sit met, conttur adiscing elit, sed do eiumod tempor incidunt ut labore et dolore magna aliqua. Ut enim ad mnim veniam, quis nostud exercitation ullamco laboris nisi ut aliquip ex ea commodo consequat. Duis aute irure door in reprehenderit in voluptate velit esse cillum doore eu fugiat nulla pariatur. Excepteur sint occecat cupiatat non proident, sunt in culpa. fugiat nulla pariatur. Excepteur sint occecat cupiatat non proident, sunt in culpa.</p>
  <div class="logo-mark">DadHarbor</div>
</section>

<footer class="footer">
  <div class="footer-kicker">CONTACT</div>
  <div class="footer-title">GET IN TOUCH</div>
  <div class="footer-email">info@dadharbor.com</div>
  <div class="footer-social">
    <span aria-label="Social link one"></span>
    <span aria-label="Social link two"></span>
    <span aria-label="Social link three"></span>
  </div>
  <div class="footer-legal">Privacy Policy &nbsp;|&nbsp; © 2013 DadHarbor &nbsp;|&nbsp; Terms Policy &nbsp;|&nbsp; Disclaimer</div>
</footer>

</body>
</html>
```